Tidy paddock Services

After a high quality design website. we are a company that provides services to people that own land and need a hand getting on top of the delayed jobs.
would want a number of tab/ pages for the web page.
Home page / About us page / services page / Gallery page. / Contact us page
we offer a wide range of services .listed below

Stock Work (title)

Stock movement
Break feeding
Temporary staffing

Spraying (title)

Spraying weeds
Spraying gorse

Pastures (title)

Fertilizing
Topping

Building (title)

Habitable sheds
Farm sheds
Sheep yards
Cattle yards
Repair farm buildings
Decks
Retaining walls

Fencing (title)

Stock fencing
Post & rail
Stock yards repair
Electric fencing install & repairs

Water Management (title)

Water trough installation
Water scheme install
Water trough cleaning
Farm water maintenance
Water ponds
Ornamental ponds
Drainage

General (title)

Lawn mowing
Hedge trimming
Pruning trees
Metaling drive ways & races
Water blasting
Small digger work
Little tip truck cartage
Home kill management
Mulching gorse
Section clearing

```html
<!DOCTYPE html>
<html lang="en">
<head>
<meta charset="utf-8">
<title>Tidy paddock Services</title>
<link href="https://fonts.googleapis.com/css2?family=Montserrat:wght@600;700;800&family=Roboto:wght@400;500;700&display=swap" rel="stylesheet">
<style>
:root{
  --green:#6b9c12;
  --green-btn:#5a9313;
  --green-deep:#3f7f1d;
  --ink:#222;
  --text:#555;
  --field:#f2f2f2;
  --footer:#000;
  --white:#fff;
}
*{box-sizing:border-box;margin:0;padding:0}
html,body{width:1200px;height:4471px;overflow:hidden;background:var(--white)}
body{font-family:'Roboto',sans-serif;color:var(--text)}
.page{position:relative;width:1200px;height:4471px;overflow:hidden}
.abs{position:absolute}
.topline{left:0;top:0;width:1200px;height:4px;background:var(--green)}
.brand{display:flex;align-items:center;gap:10px}
.brand-dot{width:34px;height:34px;border-radius:50%;background:var(--green)}
.brand-name{font-family:'Montserrat',sans-serif;font-weight:700;color:var(--green);font-size:20px;line-height:22px;text-transform:uppercase}
.header-brand{left:95px;top:26px}
.contact-pill{left:469px;top:3px;width:619px;height:44px;border-radius:0 0 22px 22px/0 0 22px 22px;background:var(--green);border-radius:22px;display:flex;align-items:center;padding:0 24px;gap:14px;color:var(--white);font-size:14px}
.contact-pill .item{display:flex;align-items:center;gap:10px}
.contact-pill .item + .item{margin-left:auto}
.contact-pill b{font-size:18px;font-weight:700}
.pill-icon{width:30px;height:30px;border-radius:50%;background:var(--white);display:flex;align-items:center;justify-content:center}
.nav{left:0;top:64px;width:1200px;height:24px}
.nav a{position:absolute;font-size:14px;color:#333;text-decoration:none}
.nav a.active{color:var(--green)}
.hero{left:0;top:106px;width:1200px;height:642px;background:linear-gradient(100deg,#3f6a22 0%,#6f9a3b 30%,#8fb45a 55%,#5d8a2c 80%,#3b6a1f 100%)}
.hero-ring{left:182px;top:238px;width:358px;height:358px;border-radius:50%;border:3px solid var(--white);background:rgba(70,110,30,.45);text-align:center;color:var(--white)}
.hero-ring h1{font-family:'Montserrat',sans-serif;font-weight:700;font-size:36px;line-height:47px;margin-top:76px;text-transform:uppercase}
.hero-ring p{font-size:21px;margin-top:10px;letter-spacing:.5px}
.btn{display:inline-flex;align-items:center;justify-content:center;gap:6px;border-radius:22px;font-family:'Roboto',sans-serif;font-weight:700;font-size:13px;text-transform:uppercase}
.hero-ring .btn{margin-top:16px;width:164px;height:40px;background:var(--white);color:var(--green)}
.scroll-btn{left:582px;top:726px;width:52px;height:52px;border-radius:50%;background:var(--white);box-shadow:0 4px 12px rgba(0,0,0,.18);display:flex;align-items:center;justify-content:center}
.section-title{font-family:'Montserrat',sans-serif;font-weight:700;color:var(--ink);font-size:44px;text-transform:uppercase;text-align:center;left:0;width:1200px}
.rule{left:576px;width:48px;height:3px;background:var(--green)}
.about-photo{left:144px;top:889px;width:399px;height:454px;border-radius:16px;background:linear-gradient(160deg,#5a4a36 0%,#4c6a2a 45%,#88ad3a 75%,#4f7a22 100%)}
.about-title{left:627px;top:872px;font-family:'Montserrat',sans-serif;font-weight:700;font-size:44px;color:var(--ink)}
.about-copy{left:627px;top:958px;width:427px;font-size:13.6px;line-height:23.1px;text-align:justify;color:var(--text)}
.about-btn{left:627px;top:1302px;width:163px;height:42px;background:var(--green-btn);color:var(--white)}
.why-band{left:0;top:1360px;width:1200px;height:688px}
.why-title{left:0;width:1200px;top:1548px;text-align:center;font-family:'Montserrat',sans-serif;font-weight:700;font-size:43px;line-height:47px;color:var(--white);text-transform:uppercase}
.why-rule{left:576px;top:1667px;width:48px;height:3px;background:#f2c200}
.why-lines{left:0;top:1700px;width:1200px;height:240px}
.why-icon{width:90px;height:90px;border-radius:50%;background:var(--white);display:flex;align-items:center;justify-content:center}
.why-text{width:180px;text-align:center;font-size:14px;line-height:21px;color:var(--white)}
.why-circle{left:369px;top:1797px;width:460px;height:460px;border-radius:50%;background:var(--white)}
.why-photo{left:383px;top:1811px;width:432px;height:432px;border-radius:50%;background:radial-gradient(circle at 30% 30%,#c9b25c 0%,#7ea23a 40%,#4d7a20 75%,#36591a 100%)}
.service-card{text-align:center}
.service-photo{width:100%}
.service-name{font-family:'Roboto',sans-serif;font-weight:500;font-size:20px;color:var(--ink)}
.service-text{font-size:13.6px;line-height:21px;color:var(--text);margin:4px auto 0;width:250px}
.slider-arrow{width:42px;height:42px;border-radius:50%;background:#e6e6e6;display:flex;align-items:center;justify-content:center;color:#555;font-size:16px}
.services-btn{left:507px;top:2909px;width:163px;height:42px;background:var(--green-deep);color:var(--white)}
.gallery{left:0;top:3168px;width:1200px;height:274px}
.field{background:var(--field);font-size:14px;color:#444;padding:0 16px;display:flex;align-items:center}
.field.area{align-items:flex-start;padding-top:20px}
.submit-btn{left:519px;top:3881px;width:163px;height:42px;background:var(--green-deep);color:var(--white)}
.footer-edge{left:0;top:4044px;width:1200px;height:11px;background:#9aa0a4}
.footer{left:0;top:4055px;width:1200px;height:416px;background:var(--footer);color:var(--white)}
.footer-brand{left:121px;top:4160px}
.social{display:flex;gap:6px;left:174px;top:4253px}
.social span{width:34px;height:34px;border-radius:50%;border:2px solid var(--green)}
.footer-col h3{font-family:'Roboto',sans-serif;font-weight:700;font-size:20px;margin-bottom:18px}
.footer-col ul{list-style:none}
.footer-col li{font-size:14px;height:25.7px}
.footer-col li::before{content:"»";margin-right:14px}
.contact-row{display:flex;gap:14px;font-size:14px;line-height:22px;margin-bottom:24px}
.contact-row .ic{flex:none;width:28px;height:28px;border-radius:50%;background:var(--green);display:flex;align-items:center;justify-content:center}
.copyright{left:0;width:1200px;top:4416px;text-align:center;font-size:13px}
</style>
</head>
<body>
<div class="page">

  <div class="abs topline"></div>
  <div class="abs brand header-brand">
    <span class="brand-dot"></span>
    <span class="brand-name">Tidy paddock<br>Services</span>
  </div>

  <div class="abs contact-pill">
    <div class="item">
      <span class="pill-icon"><svg width="14" height="14" viewBox="0 0 24 24"><path fill="#6b9c12" d="M6.6 10.8a15 15 0 0 0 6.6 6.6l2.2-2.2a1 1 0 0 1 1-.25 11.4 11.4 0 0 0 3.6.57 1 1 0 0 1 1 1V20a1 1 0 0 1-1 1A17 17 0 0 1 3 4a1 1 0 0 1 1-1h3.5a1 1 0 0 1 1 1c0 1.25.2 2.45.57 3.6a1 1 0 0 1-.25 1z"/></svg></span>
      <span>Call Us : <b>+1 555 010 4477</b></span>
    </div>
    <div class="item">
      <span class="pill-icon"><svg width="14" height="14" viewBox="0 0 24 24"><path fill="#6b9c12" d="M2 5h20v14H2zm2 2v.5l8 5 8-5V7l-8 5z"/></svg></span>
      <span>Mail Us : <b>hello@tidypaddock.co</b></span>
    </div>
  </div>

  <nav class="abs nav">
    <a class="active" style="left:694px">Home</a>
    <a style="left:769px">About Us</a>
    <a style="left:864px">Services</a>
    <a style="left:955px">Gallery</a>
    <a style="left:1036px">Contact</a>
  </nav>

  <div class="abs hero" role="img" aria-label="Gardener in work overalls clearing a lawn with a leaf blower beside flower beds"></div>
  <div class="abs hero-ring">
    <h1>Tidy paddock<br>Services</h1>
    <p>LAWN SERVICES</p>
    <span class="btn">Get a quote</span>
  </div>
  <div class="abs scroll-btn"><svg width="18" height="20" viewBox="0 0 18 20"><path d="M9 2v15M3 11l6 6 6-6" fill="none" stroke="#6b9c12" stroke-width="2.2" stroke-linecap="round"/></svg></div>

  <div class="abs about-photo" role="img" aria-label="Worker pushing a lawn mower across a garden in front of a house"></div>
  <h2 class="abs about-title">ABOUT US</h2>
  <p class="abs about-copy">Lorem ipsum dolor sit amet, consectetur adipiscing elit, sed do eiusmod tempor incididunt ut labore et dolore magna aliqua. Ut enim ad minim veniam, quis nostrud exercitation ullamco laboris nisi ut aliquip ex ea commodo consequat. Duis aute irure dolor in reprehenderit in voluptate velit esse cillum dolore eu fugiat nulla pariatur. Excepteur sint occaecat cupidatat non proident, sunt in culpa qui officia deserunt mollit anim id est laborum. Lorem ipsum dolor sit amet, consectetur adipiscing elit, sed do eiusmod tempor incididunt ut labore et dolore magna aliqua. Ut enim ad minim veniam, quis nostrud exercitation ullamco laboris nisi ut aliquip ex ea commodo consequat. Duis aute irure dolor in reprehenderit in voluptate velit esse cillum dolore eu fugiat nulla pariatur. Excepteur sint occaecat cupidatat non proident, sunt in culpa qui officia deserunt mollit anim id est laborum.</p>
  <span class="abs btn about-btn">Learn more <svg width="12" height="12" viewBox="0 0 12 12"><circle cx="6" cy="6" r="6" fill="#fff"/><path d="M5 3.5 7.5 6 5 8.5" fill="none" stroke="#5a9313" stroke-width="1.6"/></svg></span>

  <svg class="abs why-band" viewBox="0 1360 1200 688" width="1200" height="688"><path d="M0 1536 Q600 1362 1200 1536 L1200 2048 L0 2048Z" fill="#6b9c12"/></svg>
  <h2 class="abs why-title">Why choose<br>Tidy paddock Services</h2>
  <div class="abs why-rule"></div>

  <svg class="abs why-lines" viewBox="0 1700 1200 240" width="1200" height="240">
    <g fill="none" stroke="#d7e6b8" stroke-width="1.5">
      <path d="M446 1731H514V1800"/>
      <path d="M764 1731H684V1800"/>
      <path d="M324 1914H384"/>
      <path d="M884 1914H822"/>
    </g>
  </svg>

  <div class="abs why-icon" style="left:356px;top:1686px"><svg width="44" height="44" viewBox="0 0 44 44" fill="none" stroke="#6b9c12" stroke-width="2"><path d="M22 38V20M22 20c-8 0-12-6-12-12 7 0 12 5 12 12zM22 26c6 0 10-5 10-10-6 0-10 4-10 10z"/><path d="M8 38h28"/></svg></div>
  <p class="abs why-text" style="left:274px;top:1783px">Lorem ipsum dolor sit amet, consectetur</p>

  <div class="abs why-icon" style="left:764px;top:1686px"><svg width="44" height="44" viewBox="0 0 44 44" fill="none" stroke="#6b9c12" stroke-width="2"><path d="M22 38V20M22 20c-8 0-12-6-12-12 7 0 12 5 12 12zM22 26c6 0 10-5 10-10-6 0-10 4-10 10z"/><path d="M8 38h28"/></svg></div>
  <p class="abs why-text" style="left:760px;top:1783px">Lorem ipsum dolor sit amet, consectetur</p>

  <div class="abs why-icon" style="left:234px;top:1866px"><svg width="44" height="44" viewBox="0 0 44 44" fill="none" stroke="#6b9c12" stroke-width="2"><path d="M22 38V20M22 20c-8 0-12-6-12-12 7 0 12 5 12 12zM22 26c6 0 10-5 10-10-6 0-10 4-10 10z"/><path d="M8 38h28"/></svg></div>
  <p class="abs why-text" style="left:154px;top:1963px">Lorem ipsum dolor sit amet, consectetur</p>

  <div class="abs why-icon" style="left:884px;top:1866px"><svg width="44" height="44" viewBox="0 0 44 44" fill="none" stroke="#6b9c12" stroke-width="2"><path d="M22 38V20M22 20c-8 0-12-6-12-12 7 0 12 5 12 12zM22 26c6 0 10-5 10-10-6 0-10 4-10 10z"/><path d="M8 38h28"/></svg></div>
  <p class="abs why-text" style="left:880px;top:1963px">Lorem ipsum dolor sit amet, consectetur</p>

  <div class="abs why-circle"></div>
  <div class="abs why-photo" role="img" aria-label="Petrol lawn mower cutting green grass in evening sunlight"></div>

  <h2 class="abs section-title" style="top:2364px">Our services</h2>
  <div class="abs rule" style="top:2427px"></div>

  <div class="abs slider-arrow" style="left:31px;top:2642px">‹</div>
  <div class="abs slider-arrow" style="left:1123px;top:2642px">›</div>

  <div class="abs service-card" style="left:111px;top:2491px;width:314px">
    <div class="service-photo" role="img" aria-label="Lawn mower on a freshly cut lawn beside a hedge" style="height:236px;border-radius:10px 0 0 10px;background:linear-gradient(120deg,#2f3a2a 0%,#5e8a2a 40%,#89b73e 70%,#4d7a1f 100%)"></div>
    <h3 class="service-name" style="margin-top:12px">Lawn mowing</h3>
    <p class="service-text">Lorem ipsum dolor sit amet, conse ctetur adipiscing elit, sed do eiusmod tempor incididunt ut labore et dolore magna aliqua.</p>
  </div>

  <div class="abs service-card" style="left:774px;top:2491px;width:314px">
    <div class="service-photo" role="img" aria-label="Gloved hands pruning tree branches with secateurs" style="height:236px;border-radius:0 10px 10px 0;background:linear-gradient(120deg,#8aa64a 0%,#c2c77a 35%,#6d8a3a 65%,#2f4a22 100%)"></div>
    <h3 class="service-name" style="margin-top:12px">Pruning trees</h3>
    <p class="service-text">Lorem ipsum dolor sit amet, conse ctetur adipiscing elit, sed do eiusmod tempor incididunt ut labore et dolore magna aliqua.</p>
  </div>

  <div class="abs service-card" style="left:425px;top:2463px;width:349px">
    <div class="service-photo" role="img" aria-label="Hand shears trimming a green hedge" style="height:290px;border-radius:10px;box-shadow:0 6px 18px rgba(0,0,0,.25);background:radial-gradient(circle at 50% 45%,#9fd04e 0%,#5e9a24 50%,#386a1a 100%)"></div>
    <h3 class="service-name" style="margin-top:10px">Hedge trimming</h3>
    <p class="service-text">Lorem ipsum dolor sit amet, conse ctetur adipiscing elit, sed do eiusmod tempor incididunt ut labore et dolore magna aliqua.</p>
  </div>

  <span class="abs btn services-btn">Learn more <svg width="12" height="12" viewBox="0 0 12 12"><circle cx="6" cy="6" r="6" fill="#fff"/><path d="M5 3.5 7.5 6 5 8.5" fill="none" stroke="#3f7f1d" stroke-width="1.6"/></svg></span>

  <h2 class="abs section-title" style="top:3066px">Our gallery</h2>
  <div class="abs rule" style="top:3129px"></div>

  <svg class="abs gallery" viewBox="0 0 1200 274" width="1200" height="274" role="img" aria-label="Gallery strip: ride-on mower on a lawn, hedge trimming, lawn mowing, water blasting, and flower bed pruning">
    <defs>
      <linearGradient id="g1" x1="0" y1="0" x2="1" y2="1"><stop offset="0" stop-color="#4f8a2a"/><stop offset="1" stop-color="#7fb63a"/></linearGradient>
      <linearGradient id="g2" x1="0" y1="0" x2="1" y2="1"><stop offset="0" stop-color="#3e6e24"/><stop offset="1" stop-color="#8cc04a"/></linearGradient>
      <linearGradient id="g3" x1="0" y1="0" x2="0" y2="1"><stop offset="0" stop-color="#7c8f62"/><stop offset="1" stop-color="#6fa434"/></linearGradient>
      <linearGradient id="g4" x1="0" y1="0" x2="1" y2="1"><stop offset="0" stop-color="#6f9a4a"/><stop offset="1" stop-color="#4b6f3a"/></linearGradient>
      <linearGradient id="g5" x1="0" y1="0" x2="1" y2="1"><stop offset="0" stop-color="#4a6a2c"/><stop offset="1" stop-color="#9a7a5c"/></linearGradient>
    </defs>
    <polygon points="0,0 280,0 210,274 0,274" fill="url(#g1)"/>
    <polygon points="280,0 500,0 440,274 210,274" fill="url(#g2)"/>
    <polygon points="500,0 770,0 680,274 440,274" fill="url(#g3)"/>
    <polygon points="770,0 1000,0 960,274 680,274" fill="url(#g4)"/>
    <polygon points="1000,0 1200,0 1200,274 960,274" fill="url(#g5)"/>
  </svg>

  <h2 class="abs section-title" style="top:3554px">Contact us</h2>
  <div class="abs rule" style="top:3617px"></div>

  <div class="abs field" style="left:227px;top:3652px;width:240px;height:54px">Name</div>
  <div class="abs field" style="left:479px;top:3652px;width:240px;height:54px">Email</div>
  <div class="abs field" style="left:731px;top:3652px;width:241px;height:54px">Phone</div>
  <div class="abs field area" style="left:227px;top:3720px;width:745px;height:138px">Text here..</div>
  <span class="abs btn submit-btn">Submit now</span>

  <div class="abs footer-edge"></div>
  <footer class="abs footer"></footer>

  <div class="abs brand footer-brand">
    <span class="brand-dot"></span>
    <span class="brand-name">Tidy paddock<br>Services</span>
  </div>
  <div class="abs social" aria-label="Social links"><span></span><span></span><span></span></div>

  <div class="abs footer-col" style="left:444px;top:4136px;color:#fff">
    <h3>Quick Links</h3>
    <ul><li>Home</li><li>About Us</li><li>Services</li><li>BLog</li><li>Gallery</li><li>Contact</li></ul>
  </div>
  <div class="abs footer-col" style="left:642px;top:4136px;color:#fff">
    <h3>Information</h3>
    <ul><li>Privacy policy</li><li>Terms &amp; condition</li><li>Support</li><li>Faq</li><li>Reviews</li><li>Contact</li></ul>
  </div>
  <div class="abs footer-col" style="left:873px;top:4136px;width:240px;color:#fff">
    <h3>Contact Details</h3>
    <div class="contact-row"><span class="ic"><svg width="12" height="14" viewBox="0 0 12 14"><path d="M6 0a5 5 0 0 1 5 5c0 4-5 9-5 9S1 9 1 5a5 5 0 0 1 5-5z" fill="#fff"/><circle cx="6" cy="5" r="1.8" fill="#6b9c12"/></svg></span><span>123, Lorem ipsum dolor sit amet, consectetur</span></div>
    <div class="contact-row"><span class="ic"><svg width="13" height="13" viewBox="0 0 24 24"><path fill="#fff" d="M6.6 10.8a15 15 0 0 0 6.6 6.6l2.2-2.2a1 1 0 0 1 1-.25 11.4 11.4 0 0 0 3.6.57 1 1 0 0 1 1 1V20a1 1 0 0 1-1 1A17 17 0 0 1 3 4a1 1 0 0 1 1-1h3.5a1 1 0 0 1 1 1c0 1.25.2 2.45.57 3.6a1 1 0 0 1-.25 1z"/></svg></span><span>+1 555 010 4477</span></div>
    <div class="contact-row"><span class="ic"><svg width="13" height="13" viewBox="0 0 24 24"><path fill="#fff" d="M2 5h20v14H2zm2 2v.5l8 5 8-5V7l-8 5z"/></svg></span><span>hello@tidypaddock.co</span></div>
  </div>

  <p class="abs copyright" style="color:#fff">© Copyrights 2024 Tidy Paddock | All Rights Reserved</p>

</div>
</body>
</html>
```